Business Card Design Project

We are not a new company, but renamed to "Vantorin Kitchens" last year. We specialize in modern high-end cabinetry imports. We would like to communicate a sense of quality and cutting edge technology. Ideally the design would incorporate our logo colors, silver, red and preferably a black, matte background. Though we are open to suggestions.
Logo is attached.
Edit: I have attached rough drafts of the previous cards, this way you will have all necessary content that needs to go on the cards.
Updates
Project Deadline Extended
Reason: We have received a lot of great designs, but due to the sheer number we couldn't respond to all. We will extend the deadline for another 7 days to finalize and provide feedback to designers.
Thank you for your hard work!
Industry/Entity Type
Business
Look and feel
Each slider illustrates characteristics of the customer's brand and the style your logo design should communicate.

```html
<!DOCTYPE html>
<html lang="en">
<head>
<meta charset="utf-8">
<title>Vantorin Kitchens – Business Card</title>
<link rel="stylesheet" href="https://fonts.googleapis.com/css2?family=Michroma&family=Arimo:wght@400;700&display=swap">
<style>
  :root {
    --stage: #e9e9ee;
    --card: #0b0b0b;
    --silver: #c4c4c6;
    --silver-dim: #8d8d90;
    --white: #f4f4f4;
    --red: #e3131b;
    --rule: #9a9a9a;
  }
  * { box-sizing: border-box; margin: 0; padding: 0; }
  html, body {
    width: 1200px; height: 987px; overflow: hidden;
    background: var(--stage);
  }
  .stage {
    width: 1200px; height: 987px;
    display: flex; flex-direction: column; align-items: center; justify-content: center;
    gap: 44px;
  }
  .card {
    width: 760px; height: 434px;
    background: var(--card);
    border-radius: 34px;
    box-shadow: 0 10px 28px rgba(0,0,0,.22);
    position: relative;
    color: var(--white);
    font-family: "Arimo", Arial, sans-serif;
  }
  /* front */
  .brand {
    position: absolute; top: 78px; left: 0; right: 0;
    display: flex; align-items: center; justify-content: center; gap: 18px;
  }
  .brand-square {
    width: 34px; height: 34px; background: var(--silver);
  }
  .brand-name {
    font-family: "Michroma", sans-serif;
    font-size: 38px; letter-spacing: 1px;
    color: var(--silver);
    text-transform: uppercase;
  }
  .rule {
    position: absolute; left: 60px; right: 60px; height: 2px;
    background: linear-gradient(90deg, transparent, var(--rule) 20%, #d8d8d8 50%, var(--rule) 80%, transparent);
  }
  .rule.top { top: 160px; }
  .rule.bottom { top: 372px; }
  .holder {
    position: absolute; top: 186px; left: 0; right: 0; text-align: center;
    font-size: 22px; font-weight: 700; letter-spacing: .5px;
  }
  .holder .role { color: var(--red); font-weight: 400; }
  .contacts {
    position: absolute; top: 234px; left: 0; right: 0;
    text-align: center; font-size: 19px; line-height: 38px;
  }
  .contacts .item { display: inline-flex; align-items: center; gap: 6px; margin: 0 8px; }
  .contacts svg { width: 16px; height: 16px; fill: var(--white); }
  /* back */
  .back {
    display: flex; align-items: center; justify-content: center; gap: 26px;
  }
  .back .brand-square { width: 64px; height: 64px; }
  .back .brand-name { font-size: 44px; }
</style>
</head>
<body>
<main class="stage">
  <section class="card front">
    <div class="brand">
      <span class="brand-square"></span>
      <span class="brand-name">Vantorin Kitchens</span>
    </div>
    <div class="rule top"></div>
    <p class="holder">MARCUS DELANE, <span class="role">Director</span></p>
    <div class="contacts">
      <div>
        <span class="item"><svg viewBox="0 0 16 16"><path d="M3 1l3 3-1.5 2a9 9 0 0 0 5.5 5.5L12 10l3 3-2 2C7 15 1 9 1 3z"/></svg>780.555.0142</span>
        <span class="item"><svg viewBox="0 0 16 16"><rect x="1" y="6" width="14" height="8" rx="1"/><rect x="4" y="1" width="8" height="5"/></svg>780.555.0187</span>
      </div>
      <div>
        <span class="item"><svg viewBox="0 0 16 16"><rect x="4" y="1" width="8" height="14" rx="1.5"/></svg>780.555.0163</span>
        <span class="item"><svg viewBox="0 0 16 16"><path d="M1 3h14v10H1z M1 3l7 6 7-6" stroke="#0b0b0b" stroke-width="1"/></svg>marcus@vantorinkitchens.ca</span>
      </div>
      <div>2816 - 71 St. Northvale, AB T5R 2K4</div>
    </div>
    <div class="rule bottom"></div>
  </section>

  <section class="card back">
    <span class="brand-square"></span>
    <span class="brand-name">Vantorin Kitchens</span>
  </section>
</main>
</body>
</html>
```